Fitness Centre/Personal Trainer Business Card

We need a business card design for a company based in Singapore called 'Vigor Ledger'.

We are a team of Personal Trainers and we are planning to open our new training facility.

This design will also be printed/painted on the walls in our gym.

We are a new breed of personal trainers who take fitness seriously and holistically. We do not merely train our clients to be big and muscular.

We believe in wholeness. In our opinion, fitness should include: strength, speed, flexibility, mobility, stamina & agility. These are what we train for. Of course, nutrition/diet is key.

We use fitness tools such as kettlebells, QVL, Pylometric boxes, battling ropes, clubbells, medicine balls, bulgarian bags etc - functional and non-bulky tools.

I currently have a Facebook page 'Vigor Ledger SG' which shows a logo of a kettlebell. But my business focus has since changed.

Services provided:
- Kettlebell Sport Preparation
- Calisthenics Training
- Corrective Exercises
- Sports Strength & Conditioning
- 28 days Weight Loss Program
- Myofascial Rehab Therapy
- Sports/Thai Massage

Main colors for the design should be BLACK & YELLOW. We envision a design which is able to protray the holistic view we take on fitness. Also it should somewhat appeal to the ladies and not intimidate them.

Target Market(s)

People between 18-35 years old. Students and working class alike.

Industry/Entity Type

Training

Requirements
Must have
• Name: Marcus Obadiah Lim
Fitness Coach
Corrective Exercise Specialist
M: +65 9437 2065
E: marcus@sgvigorledger-example.com

Double-sided please.
Nice to have
• "What is your vigor ledger?"

```html
<!DOCTYPE html>
<html lang="en">
<head>
<meta charset="utf-8">
<title>Vigor Ledger – Business Cards</title>
<link rel="stylesheet" href="https://fonts.googleapis.com/css2?family=Open+Sans:wght@400;600;700&display=swap">
<style>
  :root{
    --ink:#0b0b0b;
    --paper:#ffffff;
    --yellow:#f5e10e;
    --yellow-text:#f2d90a;
    --stage:#9a9a9a;
    --mark-faint:rgba(180,170,60,0.18);
  }
  *{box-sizing:border-box;margin:0;padding:0}
  html,body{width:1200px;height:693px;overflow:hidden}
  body{background:var(--stage);position:relative;font-family:"Open Sans",Arial,sans-serif}
  .card{position:absolute;width:541px;height:308px;overflow:hidden}
  .card--dark{background:var(--ink);color:var(--paper)}
  .card--light{background:var(--paper);color:var(--ink);outline:1px solid #777}
  .card--front-dark{left:41px;top:23px}
  .card--front-light{left:625px;top:23px}
  .card--back-dark{left:41px;top:359px}
  .card--back-light{left:625px;top:359px}
  .wave{position:absolute;left:0;top:0;width:541px;height:308px}
  .brand{position:absolute;left:52px;top:118px;display:flex;align-items:center;gap:9px}
  .brand__dot{width:20px;height:20px;border-radius:50%;background:var(--yellow)}
  .brand__name{font-size:26px;font-weight:700;color:var(--yellow-text)}
  .card--light .brand__name{color:var(--ink)}
  .card--light .brand__dot{background:var(--ink)}
  .card--back-dark .brand{left:34px;top:124px;gap:8px}
  .card--back-dark .brand__name{font-size:23px}
  .card--back-dark .brand__dot{width:18px;height:18px}
  .identity{position:absolute;right:26px;top:40px;text-align:right;line-height:1.3}
  .identity__name{font-size:18px;font-weight:700}
  .card--dark .identity__name{color:var(--yellow-text)}
  .identity__role{font-size:14.5px}
  .contact{position:absolute;right:26px;top:216px;text-align:right;font-size:14px;line-height:24px;color:var(--ink)}
  .contact li{list-style:none;display:flex;justify-content:flex-end;align-items:center;gap:6px}
  .contact svg{width:12px;height:12px}
  .services{position:absolute;left:270px;top:16px}
  .services__title{font-size:18px;font-weight:700;margin-bottom:10px}
  .services__list{list-style:none;font-size:15px;line-height:26px}
  .services__list li::before{content:"•";margin-right:4px}
  .question{position:absolute;left:0;right:0;text-align:center;font-weight:700}
  .card--back-dark .question{bottom:24px;left:140px;font-size:16px;color:var(--yellow-text);letter-spacing:1px}
  .card--back-light .question{bottom:12px;font-size:15px}
  .ghost-mark{position:absolute;left:0;right:0;top:130px;text-align:center;font-size:44px;font-weight:700;color:var(--mark-faint)}
  .services--centered{left:0;right:0;top:66px;text-align:center}
  .services--centered .services__title{margin-bottom:14px}
  .services--centered .services__list{font-size:16.5px;line-height:33px}
  .services--centered li::before{content:none}
  .services--centered span{margin:0 2px}
  .services--centered span::before{content:"•";margin-right:4px}
</style>
</head>
<body>

<section class="card card--dark card--front-dark">
  <svg class="wave" viewBox="0 0 541 308" aria-hidden="true">
    <path d="M0,231 C60,251 150,256 260,206 C340,170 440,151 541,144 L541,308 L0,308 Z" fill="#fff"/>
    <path d="M0,253 C60,273 150,278 260,228 C340,192 440,173 541,166 L541,308 L0,308 Z" fill="#0b0b0b"/>
    <path d="M0,265 C60,285 150,290 260,240 C340,204 440,185 541,178 L541,308 L0,308 Z" fill="var(--yellow)"/>
    <path d="M20,300 C100,300 180,286 250,256" fill="none" stroke="#0b0b0b" stroke-width="2"/>
  </svg>
  <div class="brand"><span class="brand__dot"></span><span class="brand__name">Vigor Ledger</span></div>
  <div class="identity">
    <p class="identity__name">Marcus Obadiah Lim</p>
    <p class="identity__role">Fitness Coach</p>
    <p class="identity__role">Corrective Exercise Specialist</p>
  </div>
  <ul class="contact">
    <li><svg viewBox="0 0 12 12"><rect x="3" y="0.5" width="6" height="11" rx="1" fill="none" stroke="#0b0b0b"/><rect x="4.5" y="2" width="3" height="4" fill="#0b0b0b"/></svg>+65 9437 2065</li>
    <li><svg viewBox="0 0 12 12"><rect x="0.5" y="2.5" width="11" height="7" fill="none" stroke="#0b0b0b"/><path d="M0.5,2.5 L6,7 L11.5,2.5" fill="none" stroke="#0b0b0b"/></svg>marcus@sgvigorledger-example.com</li>
    <li><svg viewBox="0 0 12 12"><circle cx="6" cy="6" r="5.3" fill="none" stroke="#0b0b0b"/><ellipse cx="6" cy="6" rx="2.3" ry="5.3" fill="none" stroke="#0b0b0b"/><path d="M0.7,6 H11.3" stroke="#0b0b0b"/></svg>www.sgvigor-example.com</li>
  </ul>
</section>

<section class="card card--light card--front-light">
  <svg class="wave" viewBox="0 0 541 308" aria-hidden="true">
    <path d="M0,237 C60,257 150,262 260,212 C340,176 440,157 541,150 L541,308 L0,308 Z" fill="#0b0b0b"/>
    <path d="M0,255 C60,275 150,280 260,230 C340,194 440,175 541,168 L541,308 L0,308 Z" fill="#fff"/>
    <path d="M0,265 C60,285 150,290 260,240 C340,204 440,185 541,178 L541,308 L0,308 Z" fill="var(--yellow)"/>
    <path d="M20,298 C100,298 180,284 250,256" fill="none" stroke="#fff" stroke-width="2"/>
  </svg>
  <div class="brand"><span class="brand__dot"></span><span class="brand__name">Vigor Ledger</span></div>
  <div class="identity">
    <p class="identity__name">Marcus Obadiah Lim</p>
    <p class="identity__role">Fitness Coach</p>
    <p class="identity__role">Corrective Exercise Specialist</p>
  </div>
  <ul class="contact">
    <li><svg viewBox="0 0 12 12"><rect x="3" y="0.5" width="6" height="11" rx="1" fill="none" stroke="#0b0b0b"/><rect x="4.5" y="2" width="3" height="4" fill="#0b0b0b"/></svg>+65 9437 2065</li>
    <li><svg viewBox="0 0 12 12"><rect x="0.5" y="2.5" width="11" height="7" fill="none" stroke="#0b0b0b"/><path d="M0.5,2.5 L6,7 L11.5,2.5" fill="none" stroke="#0b0b0b"/></svg>marcus@sgvigorledger-example.com</li>
    <li><svg viewBox="0 0 12 12"><circle cx="6" cy="6" r="5.3" fill="none" stroke="#0b0b0b"/><ellipse cx="6" cy="6" rx="2.3" ry="5.3" fill="none" stroke="#0b0b0b"/><path d="M0.7,6 H11.3" stroke="#0b0b0b"/></svg>www.sgvigor-example.com</li>
  </ul>
</section>

<section class="card card--dark card--back-dark">
  <div class="brand"><span class="brand__dot"></span><span class="brand__name">Vigor Ledger</span></div>
  <div class="services">
    <h2 class="services__title">Services</h2>
    <ul class="services__list">
      <li>Sports Strength &amp; Conditioning</li>
      <li>Kettlebell Sport Preparation</li>
      <li>28 days Weight Loss Program</li>
      <li>Myofascial Rehab Therapy</li>
      <li>Calisthenics Training</li>
      <li>Corrective Exercises</li>
      <li>Sports/Thai Massage</li>
    </ul>
  </div>
  <p class="question">What is your vigor ledger ?</p>
</section>

<section class="card card--light card--back-light">
  <p class="ghost-mark">Vigor Ledger</p>
  <div class="services services--centered">
    <h2 class="services__title">Services</h2>
    <ul class="services__list">
      <li><span>Sports Strength &amp; Conditioning</span> <span>Sports/Thai Massage</span></li>
      <li><span>Kettlebell Sport Preparation</span> <span>Corrective Exercises</span></li>
      <li><span>28 days Weight Loss Program</span> <span>Calisthenics Training</span></li>
      <li><span>Myofascial Rehab Therapy</span></li>
    </ul>
  </div>
  <p class="question">What is your vigor ledger ?</p>
</section>

</body>
</html>
```